Business Card Design Project

I need a business card designed from scratch. I have an existing logo that I can upload in Illustrator for modification or redesign.

The Company is called Query Lanterns http://querylanterns.com.au and we provide Search Engine Optimization services to Australian businesses. The current logo signifies an increase in visitors, profits etc...

There are no restrictions as to the redesign - colours, style etc are all open to change.

Cards will be full colour and one sided printed at http://www.cardmoxel.com.au so check their requirements for file format and sizes etc.

I will expect all original files upon completion of project.

Target Market(s)

Any business with a web site looking to improve their search engine rankings

Industry/Entity Type

Business

Requirements
Must have
• I like modern, sleek designs. Clean, not fussy, uncluttered.

```html
<!DOCTYPE html>
<html lang="en">
<head>
<meta charset="utf-8">
<title>Query Lanterns – Business Card</title>
<link rel="stylesheet" href="https://fonts.googleapis.com/css2?family=Source+Sans+3:wght@400;600;700&display=swap">
<style>
  :root {
    --backdrop: #e9e6df;
    --card-white: #ffffff;
    --brand-blue: #1b75bc;
    --panel-blue-light: #2c6aae;
    --panel-blue-dark: #163c70;
    --accent-yellow: #f2c21b;
    --accent-orange: #f5a21b;
    --ink: #2b2b2b;
    --card-radius: 24px;
  }
  * { box-sizing: border-box; margin: 0; padding: 0; }
  html, body {
    width: 1200px; height: 686px; overflow: hidden;
    background: var(--backdrop);
    font-family: "Source Sans 3", "Myriad Pro", Arial, sans-serif;
  }
  .canvas { position: relative; width: 1200px; height: 686px; }
  .card {
    position: absolute; width: 451px; height: 257px;
    border-radius: var(--card-radius); overflow: hidden;
    background: var(--card-white);
    box-shadow: 0 2px 5px rgba(0,0,0,.25);
  }
  .card--front { left: 101px; top: 148px; }
  .card--back  { left: 607px; top: 285px; }
  .card__panel { position: absolute; inset: 0; width: 100%; height: 100%; }

  .brand { position: absolute; display: flex; align-items: center; }
  .brand__dot {
    border-radius: 50%; background: var(--accent-yellow);
    border: 4px solid var(--card-white); flex: none;
  }
  .brand__name { color: var(--brand-blue); font-weight: 700; line-height: 1; white-space: nowrap; }

  .card--front .brand { left: 100px; top: 64px; gap: 12px; }
  .card--front .brand__dot { width: 38px; height: 38px; }
  .card--front .brand__name { font-size: 30px; }

  .card--back .brand { left: 186px; top: 110px; gap: 12px; }
  .card--back .brand__dot { width: 44px; height: 44px; }
  .card--back .brand__name { font-size: 27px; }

  .person { position: absolute; left: 160px; top: 116px; display: flex; align-items: center; }
  .person__name { color: var(--brand-blue); font-weight: 700; font-size: 19px; }
  .person__divider { width: 1px; height: 16px; background: #9aa3ad; margin: 0 8px 0 9px; }
  .person__title { color: var(--accent-yellow); font-weight: 700; font-size: 13px; }

  .contact { position: absolute; left: 160px; top: 150px; list-style: none; }
  .contact__item {
    display: flex; align-items: center; gap: 5px;
    font-size: 13.5px; color: var(--ink); height: 17.5px;
  }
  .contact__icon { width: 11px; height: 11px; fill: var(--brand-blue); flex: none; }
  .address { position: absolute; left: 163px; top: 210px; font-size: 13.5px; color: var(--ink); }
</style>
</head>
<body>
<main class="canvas">

  <section class="card card--front" aria-label="Card front">
    <svg class="card__panel" viewBox="0 0 451 257" aria-hidden="true">
      <defs>
        <radialGradient id="panelGlowFront" cx="0.45" cy="0.5" r="0.75">
          <stop offset="0" stop-color="var(--panel-blue-light)"/>
          <stop offset="1" stop-color="var(--panel-blue-dark)"/>
        </radialGradient>
      </defs>
      <polygon points="0,0 150,0 59,257 0,257" fill="var(--accent-yellow)"/>
      <polygon points="0,0 146,0 56,257 0,257" fill="url(#panelGlowFront)"/>
      <polygon points="62,246 67,232 64,257 58,257" fill="var(--accent-orange)"/>
    </svg>

    <div class="brand">
      <span class="brand__dot"></span>
      <span class="brand__name">Query Lanterns</span>
    </div>

    <div class="person">
      <span class="person__name">Your Name</span>
      <span class="person__divider"></span>
      <span class="person__title">Title</span>
    </div>

    <ul class="contact">
      <li class="contact__item">
        <svg class="contact__icon" viewBox="0 0 12 12"><path d="M2.4 0.6 4.2 2.8 3.3 4.2C3.9 5.7 5.4 7.6 7.3 8.6L8.6 7.7 11 9.4 10 11.2C6 11.4 0.8 6.3 0.7 2Z"/></svg>
        123-456-7890
      </li>
      <li class="contact__item">
        <svg class="contact__icon" viewBox="0 0 12 12"><path d="M0 2.5H12V10H0Z M0.8 3.2 6 7 11.2 3.2" stroke="#fff" stroke-width="0.9"/></svg>
        inquiry@querylanterns.com.au.com
      </li>
      <li class="contact__item">
        <svg class="contact__icon" viewBox="0 0 12 12"><circle cx="6" cy="6" r="5.6"/><path d="M0.6 6H11.4M6 0.5V11.5M2 3H10M2 9H10" stroke="#fff" stroke-width="0.8" fill="none"/><ellipse cx="6" cy="6" rx="2.4" ry="5.5" stroke="#fff" stroke-width="0.8" fill="none"/></svg>
        www.querylanterns.com.au
      </li>
    </ul>

    <p class="address">Street name City, State, zip code</p>
  </section>

  <section class="card card--back" aria-label="Card back">
    <svg class="card__panel" viewBox="0 0 451 257" aria-hidden="true">
      <defs>
        <radialGradient id="panelGlowBack" cx="0.4" cy="0.3" r="0.8">
          <stop offset="0" stop-color="var(--panel-blue-light)"/>
          <stop offset="1" stop-color="var(--panel-blue-dark)"/>
        </radialGradient>
      </defs>
      <polygon points="0,0 264,0 176,257 0,257" fill="var(--accent-yellow)"/>
      <polygon points="0,0 260,0 173,257 0,257" fill="url(#panelGlowBack)"/>
      <polygon points="182,238 188,222 182,257 176,257" fill="var(--accent-orange)"/>
    </svg>

    <div class="brand">
      <span class="brand__dot"></span>
      <span class="brand__name">Query Lanterns</span>
    </div>
  </section>

</main>
</body>
</html>
```